Business card por a urban DJ, up scale audience target

Need a sober design, modern, conservative colors but i can consider some options, y play rnb, hip hop, EDM and top40.

Business card for contact and personal info, double sided, use logo attrached please; im 42 so i need a card acording to my age an target audience.

Target Market(s)

Adult people, up scale audience

Industry/Entity Type

Music Download

Contact Information for Business Card

Cel (318) 4207265518 www.lumadrift.com

Requirements
Must have
• open mind
Nice to have
• open mind
Should not have
• DJ

```html
<!DOCTYPE html>
<html lang="en">
<head>
<meta charset="UTF-8">
<title>Luma Business Card</title>
<link rel="stylesheet" href="https://fonts.googleapis.com/css2?family=Montserrat:wght@300;400;700;800&display=swap">
<style>
  :root {
    --backdrop: #e6e2dc;
    --card-white: #ffffff;
    --ink: #232323;
    --strip-grey: #8c8c8c;
    --strip-black: #1f1f1f;
    --text-light: #ffffff;
    --shadow: rgba(0, 0, 0, 0.28);
  }
  * { margin: 0; padding: 0; box-sizing: border-box; }
  html, body {
    width: 1200px;
    height: 950px;
    overflow: hidden;
    background: var(--backdrop);
    font-family: "Montserrat", sans-serif;
  }
  .stage {
    width: 1200px;
    height: 950px;
    display: flex;
    align-items: center;
    justify-content: center;
  }
  .card {
    position: relative;
    width: 900px;
    height: 514px;
    background: var(--card-white);
    box-shadow: 0 18px 40px var(--shadow);
    overflow: hidden;
  }
  .brand {
    position: absolute;
    left: 0;
    top: 0;
    width: 900px;
    height: 394px;
    display: flex;
    align-items: center;
    justify-content: center;
    gap: 18px;
  }
  .brand-mark {
    width: 30px;
    height: 30px;
    background: var(--ink);
  }
  .brand-name {
    font-weight: 800;
    font-size: 104px;
    letter-spacing: 4px;
    color: var(--ink);
    line-height: 1;
  }
  .bottom-strip {
    position: absolute;
    left: 0;
    bottom: 0;
    width: 900px;
    height: 120px;
    display: flex;
    align-items: flex-end;
  }
  .identity-panel {
    width: 400px;
    height: 120px;
    background: var(--strip-black);
    color: var(--text-light);
    display: flex;
    flex-direction: column;
    justify-content: center;
    padding-left: 34px;
    gap: 4px;
  }
  .contact-panel {
    flex: 1;
    height: 110px;
    margin-left: 6px;
    background: var(--strip-grey);
    color: var(--text-light);
    display: flex;
    flex-direction: column;
    justify-content: center;
    align-items: flex-end;
    padding-right: 34px;
    gap: 6px;
  }
  .person-name {
    font-weight: 700;
    font-size: 30px;
    letter-spacing: 0.5px;
    white-space: nowrap;
  }
  .person-title {
    font-weight: 300;
    font-size: 24px;
    white-space: nowrap;
  }
  .phone, .website {
    font-weight: 300;
    font-size: 24px;
    letter-spacing: 0.5px;
    white-space: nowrap;
  }
</style>
</head>
<body>
  <main class="stage">
    <article class="card card-front">
      <div class="brand">
        <span class="brand-mark"></span>
        <span class="brand-name">LUMA</span>
      </div>
      <footer class="bottom-strip">
        <section class="identity-panel">
          <span class="person-name">MARCUS HALE</span>
          <span class="person-title">CEO/FOUNDER</span>
        </section>
        <section class="contact-panel">
          <span class="phone">(318) 4207265518</span>
          <span class="website">www.lumadrift.com</span>
        </section>
      </footer>
    </article>
  </main>
</body>
</html>
```